Postcard design to acquire new clients for my Property Management Company

I'm looking for a postcard design that I can send to prospective clients detailing information about my company and services.
Postcard should be eye catching and contain information from www.bramblecrestpm.com. I've provided a few screen shots for the most important information and my logo.
Target Market(s)
Real Estate
Industry/Entity Type
Real Estate
Font styles to use
Sans Serif
Requirements
Must have
- Must be eye catching!! this will be a direct mail piece - I'd like for the card to be read and not tossed in the trash immediately.
Design que from the logo.
A place to write / print the receipts name and address.
our physical address - 2387 Hollow Pine Road, Lubbock, TX 79852.
Should not have
- the contact information on the business card is not accurate - please use info from website.

```html
<!DOCTYPE html>
<html lang="en">
<head>
<meta charset="utf-8">
<title>Bramblecrest Property Management – Postcard</title>
<link rel="stylesheet" href="https://fonts.googleapis.com/css2?family=Roboto:wght@400;500;700&family=Roboto+Condensed:wght@400;500;700&display=swap">
<style>
  :root{
    --navy:#0c3463;
    --navy-deep:#082a52;
    --blue:#1d5c9b;
    --grey:#c9cacc;
    --grey-dark:#8a8c8f;
    --panel:#f2f2f2;
    --text:#4a4a4a;
    --white:#ffffff;
    --canvas:#e6e6e6;
  }
  *{box-sizing:border-box;margin:0;padding:0}
  html,body{width:1078px;height:1200px;overflow:hidden;background:var(--canvas);font-family:"Roboto",Arial,sans-serif;color:var(--text)}
  .card{position:absolute;left:128px;width:800px;height:500px;background:var(--white);overflow:hidden;box-shadow:0 4px 10px rgba(0,0,0,.25)}
  .card--front{top:85px}
  .card--back{top:626px}

  .brand{position:absolute;color:var(--navy);font-weight:500;line-height:1}
  .brand__name{font-size:34px;letter-spacing:4.5px;white-space:nowrap}
  .brand__sub{font-size:16.5px;letter-spacing:3.6px;margin-top:6px;white-space:nowrap}

  /* front */
  .hero-photo{position:absolute;left:365px;top:0;width:435px;height:297px;background:linear-gradient(110deg,#b23a35 0%,#8a2a2a 30%,#4d4f55 55%,#c9c0b4 100%);clip-path:polygon(60px 0,100% 0,100% 100%,0 100%)}
  .hero-stripe{position:absolute;left:355px;top:0;width:80px;height:297px;background:var(--grey-dark);clip-path:polygon(60px 0,75px 0,15px 100%,0 100%)}
  .headline{position:absolute;left:0;top:130px;width:412px;height:86px;background:linear-gradient(90deg,var(--navy-deep),var(--blue));clip-path:polygon(0 0,100% 0,94% 100%,0 100%);color:var(--white);font-weight:500;font-size:27px;line-height:34px;padding:10px 0 0 24px}
  .tagline{position:absolute;left:27px;top:236px;font-size:18px;line-height:23px;color:#555}
  .services{position:absolute;left:0;top:305px;width:800px;height:155px;background:linear-gradient(90deg,#0e3a6d,#0a2d58 50%,#0e3a6d);display:flex;padding:0 5px}
  .service{width:99px;text-align:center;color:var(--white)}
  .service__icon{width:60px;height:60px;margin:12px auto 0;border:3px solid var(--white);border-radius:50%;background:var(--blue);display:flex;align-items:center;justify-content:center}
  .service__title{font-size:9.5px;font-weight:700;margin-top:12px}
  .service__text{font-size:7.8px;line-height:9.6px;margin-top:6px;padding:0 4px}
  .contact-bar{position:absolute;left:0;top:460px;width:800px;height:40px;background:var(--grey);display:flex;align-items:center}
  .contact-bar__phone{display:flex;align-items:center;gap:8px;width:300px;padding-left:28px;font-family:"Roboto Condensed",Arial,sans-serif;font-weight:500;font-size:26px;color:var(--navy)}
  .contact-bar__divider{position:absolute;left:298px;top:0;width:14px;height:40px;background:var(--navy);clip-path:polygon(9px 0,14px 0,5px 100%,0 100%)}
  .contact-bar__item{display:flex;align-items:center;gap:6px;font-size:16px;color:var(--white);margin-left:28px;white-space:nowrap}

  /* back */
  .back-panel{position:absolute;left:0;top:0;width:465px;height:500px;background:var(--panel)}
  .pricing-tab{position:absolute;left:0;top:104px;width:170px;height:30px;background:var(--navy);clip-path:polygon(0 0,155px 0,170px 100%,0 100%);color:var(--white);font-size:22px;font-weight:500;padding:4px 0 0 27px}
  .plan{position:absolute;width:138px;background:var(--white);box-shadow:0 1px 6px rgba(0,0,0,.2)}
  .plan__head{background:var(--navy);color:var(--white);font-size:13px;font-weight:500;text-align:center;height:27px;line-height:27px}
  .plan__price{text-align:center;color:var(--navy);font-size:29px;font-weight:500;margin-top:10px;line-height:1}
  .plan__unit{text-align:center;font-size:7px;color:#666;margin-top:2px}
  .plan__list{list-style:none;margin:14px 0 0 7px}
  .plan__list li{font-size:7.3px;line-height:14px;color:#444;display:flex;align-items:center;gap:5px}
  .plan__list li::before{content:"";width:5px;height:3px;border-left:1.5px solid var(--navy);border-bottom:1.5px solid var(--navy);transform:rotate(-45deg) translateY(-1px)}
  .plan__badge{position:absolute;left:18px;top:-13px;width:102px;height:13px;background:var(--grey);border-radius:3px 3px 0 0;font-size:7px;text-align:center;line-height:13px;color:#555}
  .cta{position:absolute;left:0;top:377px;width:465px;height:123px;background:linear-gradient(90deg,var(--navy-deep),var(--blue) 60%,var(--navy))}
  .cta__title{position:absolute;left:23px;top:14px;color:var(--white);font-family:"Roboto Condensed",Arial,sans-serif;font-size:18px;font-weight:500;letter-spacing:.3px;white-space:nowrap}
  .cta__bar{position:absolute;left:0;top:43px;width:402px;height:42px;background:var(--grey);clip-path:polygon(0 0,388px 0,402px 100%,0 100%);display:flex;align-items:center;gap:8px;padding-left:21px;font-family:"Roboto Condensed",Arial,sans-serif;font-weight:500;font-size:28px;color:var(--white);white-space:nowrap}
  .cta__links{position:absolute;left:26px;top:95px;display:flex;gap:20px;color:var(--white);font-size:15px;white-space:nowrap}
  .cta__links span{display:flex;align-items:center;gap:6px}
  .mailing{position:absolute;left:504px;top:58px;color:var(--navy);font-size:13.5px;line-height:17px;font-style:normal}
  .mailing__name{font-size:17px;font-weight:500}
  .stamp-box{position:absolute;left:654px;top:38px;width:127px;height:87px;border:1px solid #aaa}
  .address-line{position:absolute;left:496px;width:294px;height:1px;background:#9a9a9a}
</style>
</head>
<body>

<section class="card card--front">
  <div class="brand" style="left:22px;top:58px">
    <div class="brand__name">BRAMBLECREST</div>
    <div class="brand__sub">PROPERTY MANAGEMENT</div>
  </div>
  <div class="hero-stripe"></div>
  <div class="hero-photo" role="img" aria-label="Photo of a couple receiving house keys"></div>
  <h1 class="headline">PROPERTY MANAGEMENT<br>ACROSS LUBBOCK, TX</h1>
  <p class="tagline">Maximize your financial returns with<br>support from our rental specialists</p>

  <div class="services">
    <div class="service"><div class="service__icon"><svg width="28" height="26" viewBox="0 0 28 26"><path d="M14 2 2 13h4v11h6v-7h4v7h6V13h4z" fill="#fff"/></svg></div><div class="service__title">Property Marketing</div><div class="service__text">Let us take over your marketing for you and we'll find a qualified renter quickly.</div></div>
    <div class="service"><div class="service__icon"><svg width="32" height="22" viewBox="0 0 32 22"><circle cx="10" cy="6" r="5" fill="#fff"/><circle cx="22" cy="6" r="5" fill="#fff"/><path d="M1 21c0-6 4-9 9-9s9 3 9 9zM14 21c0-6 3-9 8-9s9 3 9 9z" fill="#fff"/></svg></div><div class="service__title">Tenant Screening</div><div class="service__text">We screen all applications using fair housing guidelines to protect you.</div></div>
    <div class="service"><div class="service__icon"><svg width="20" height="30" viewBox="0 0 20 30"><text x="10" y="25" text-anchor="middle" font-family="Roboto,Arial,sans-serif" font-size="30" font-weight="700" fill="#fff">$</text></svg></div><div class="service__title">Rent Collection</div><div class="service__text">We keep your tenants current, say hello to consistent payments.</div></div>
    <div class="service"><div class="service__icon"><svg width="28" height="28" viewBox="0 0 28 28"><path d="M6 24 18 12" stroke="#fff" stroke-width="3.5" stroke-linecap="round"/><path d="M12 8l6-5 7 7-5 6z" fill="#fff"/></svg></div><div class="service__title">Maintenance</div><div class="service__text">Let us coordinate repair work on your behalf!</div></div>
    <div class="service"><div class="service__icon"><svg width="26" height="26" viewBox="0 0 26 26"><circle cx="11" cy="11" r="7" stroke="#fff" stroke-width="3" fill="none"/><path d="M16 16l7 7" stroke="#fff" stroke-width="4" stroke-linecap="round"/></svg></div><div class="service__title">Property Inspections</div><div class="service__text">We visit every home in our portfolio regularly. We have proactive property management approach.</div></div>
    <div class="service"><div class="service__icon"><svg width="28" height="24" viewBox="0 0 28 24"><path d="M2 2v20h24" stroke="#fff" stroke-width="2" fill="none"/><path d="M8 18v-6M12 18V8M16 18v-8M20 18V6" stroke="#fff" stroke-width="2.5"/></svg></div><div class="service__title">Financial Reporting</div><div class="service__text">We generate monthly statements so you can review income &amp; expenses at a moment's notice.</div></div>
    <div class="service"><div class="service__icon"><svg width="24" height="28" viewBox="0 0 24 28"><path d="M12 2 2 6v8c0 6 4 10 10 12 6-2 10-6 10-12V6z" fill="#fff"/><path d="M12 5v18c-4-2-7-5-7-9V8z" fill="#1d5c9b"/></svg></div><div class="service__title">Evictions</div><div class="service__text">We will handle evictions for you &amp; find new renters when its over.</div></div>
    <div class="service"><div class="service__icon"><svg width="30" height="28" viewBox="0 0 30 28"><path d="M15 3v20M6 26h18M4 7h22" stroke="#fff" stroke-width="2.2"/><path d="M1 16l4-8 4 8zM21 16l4-8 4 8z" fill="none" stroke="#fff" stroke-width="1.6"/><path d="M1 16h8a4 4 0 0 1-8 0zM21 16h8a4 4 0 0 1-8 0z" fill="#fff"/></svg></div><div class="service__title">Legal Guidance</div><div class="service__text">Many ordinances and housing laws governing your relationship with your tenants.</div></div>
  </div>

  <div class="contact-bar">
    <div class="contact-bar__phone"><svg width="20" height="24" viewBox="0 0 20 24"><rect x="5" y="1" width="12" height="22" rx="2" fill="#0c3463"/><rect x="7" y="4" width="8" height="14" fill="#c9cacc"/><path d="M1 10c0 5 2 8 5 10" stroke="#0c3463" stroke-width="2" fill="none"/></svg>(806) 555-0147</div>
    <div class="contact-bar__divider"></div>
    <div class="contact-bar__item"><svg width="14" height="11" viewBox="0 0 14 11"><rect width="14" height="11" rx="1" fill="#0c3463"/><path d="M1 1l6 5 6-5" stroke="#fff" fill="none"/></svg>info@bramblecrestpm.com</div>
    <div class="contact-bar__item"><svg width="14" height="14" viewBox="0 0 14 14"><circle cx="7" cy="7" r="7" fill="#0c3463"/><circle cx="7" cy="7" r="4" fill="none" stroke="#fff"/><path d="M3 7h8M7 3v8" stroke="#fff"/></svg>www.bramblecrestpm.com</div>
  </div>
</section>

<section class="card card--back">
  <div class="back-panel"></div>
  <div class="brand" style="left:22px;top:38px">
    <div class="brand__name">BRAMBLECREST</div>
    <div class="brand__sub">PROPERTY MANAGEMENT</div>
  </div>
  <h2 class="pricing-tab">PRICING</h2>

  <div class="plan" style="left:23px;top:146px;height:206px">
    <div class="plan__head">LEASE ONLY</div>
    <div class="plan__price">9%</div>
    <div class="plan__unit">of annual lease</div>
    <ul class="plan__list">
      <li>Professional Photography</li><li>Marketing &amp; Advertising</li><li>Property Showings</li><li>Tenant Screening &amp; Qualifications</li><li>Lease Execution</li><li>Move In Coordination</li>
    </ul>
  </div>
  <div class="plan" style="left:169px;top:141px;height:220px">
    <div class="plan__badge">Our Most Popular</div>
    <div class="plan__head">FULL SERVICE</div>
    <div class="plan__price">10%</div>
    <div class="plan__unit">of monthly rent</div>
    <ul class="plan__list">
      <li>Includes Leasing Service</li><li>24/7 Emergency Response</li><li>Move In &amp; Out Inspections</li><li>Professional Lease Enforcement</li><li>Schedule &amp; Oversee all Repairs</li><li>Pay all Invoices</li><li>Monthly &amp; Year End Statements</li><li>Annual Market Rent Analysis</li>
    </ul>
  </div>
  <div class="plan" style="left:313px;top:146px;height:206px">
    <div class="plan__head">PREMIUM SERVICE</div>
    <div class="plan__price">12%</div>
    <div class="plan__unit">of monthly rent</div>
    <ul class="plan__list">
      <li>Includes Full Service Features</li><li>Professional Video Marketing</li><li>Home Warranty Coordination</li><li>Tenant Retention Program</li>
    </ul>
  </div>

  <div class="cta">
    <div class="cta__title">CHOOSE THE RIGHT PROPERTY MANAGEMENT SYSTEM</div>
    <div class="cta__bar">CONTACT US <svg width="20" height="24" viewBox="0 0 20 24"><rect x="5" y="1" width="12" height="22" rx="2" fill="#fff"/><rect x="7" y="4" width="8" height="14" fill="#c9cacc"/><path d="M1 10c0 5 2 8 5 10" stroke="#fff" stroke-width="2" fill="none"/></svg> (806) 555-0147</div>
    <div class="cta__links">
      <span><svg width="14" height="11" viewBox="0 0 14 11"><rect width="14" height="11" rx="1" fill="#c9cacc"/><path d="M1 1l6 5 6-5" stroke="#0c3463" fill="none"/></svg>info@bramblecrestpm.com</span>
      <span><svg width="14" height="14" viewBox="0 0 14 14"><circle cx="7" cy="7" r="7" fill="#c9cacc"/><circle cx="7" cy="7" r="4" fill="none" stroke="#0c3463"/><path d="M3 7h8M7 3v8" stroke="#0c3463"/></svg>www.bramblecrestpm.com</span>
    </div>
  </div>

  <address class="mailing">
    <div class="mailing__name">BRAMBLECREST</div>
    2387 Hollow Pine Road,<br>Lubbock, TX 79852
  </address>
  <div class="stamp-box"></div>
  <div class="address-line" style="top:204px"></div>
  <div class="address-line" style="top:263px"></div>
  <div class="address-line" style="top:315px"></div>
</section>

</body>
</html>
```